Tallowmere Comfort Business Card Design

Design new, 2 sides, business cards for a residential and light commercial heating, air conditioning contractor.

Target Market(s)

Homeowners, small businesses

Industry/Entity Type

Business

Contact Information for Business Card

Dominic Westerhall
Phone - 862-415-2736
Email
Address - PO box 518
Brightwater NJ 07912
Website - www.TallowmereLLC.example

Requirements
Must have
• logo, company colors, standard size with no die cut, so I can use nova stamp

```html
<!DOCTYPE html>
<html lang="en">
<head>
<meta charset="utf-8">
<title>Tallowmere Comfort Business Card</title>
<link rel="stylesheet" href="https://fonts.googleapis.com/css2?family=Barlow+Semi+Condensed:wght@400;500;600&family=Roboto:wght@400&display=swap">
<style>
  :root {
    --backdrop: #e6e6e6;
    --card: #f4f4f2;
    --maroon: #7d2333;
    --gold: #f2c34c;
    --ink: #3a2a2e;
    --icon: #d23a2a;
  }
  * { box-sizing: border-box; margin: 0; padding: 0; }
  html, body { width: 1200px; height: 576px; overflow: hidden; }
  body { background: var(--backdrop); position: relative; }

  .card {
    position: absolute;
    top: 138px;
    height: 294px;
    background: var(--card);
    box-shadow: 0 2px 6px rgba(0,0,0,0.18);
  }
  .card--front { left: 81px; width: 485px; }
  .card--back { left: 602px; width: 482px; height: 291px; }

  .brand-name {
    position: absolute;
    left: 0; right: 0;
    height: 48px;
    font-family: "Barlow Semi Condensed", sans-serif;
    font-weight: 600;
    color: var(--maroon);
    display: flex;
    align-items: center;
    justify-content: center;
    gap: 12px;
    white-space: nowrap;
  }
  .brand-name__dot {
    width: 14px; height: 14px;
    border-radius: 50%;
    background: var(--maroon);
    flex: none;
  }
  .card--front .brand-name { top: 110px; font-size: 40px; }
  .card--back .brand-name { top: 78px; font-size: 36px; }

  .service-band {
    position: absolute;
    left: 0; right: 0;
    top: 247px;
    height: 27px;
    background: var(--maroon);
    color: var(--gold);
    font-family: "Roboto", sans-serif;
    font-size: 12.5px;
    line-height: 27px;
    text-align: center;
    white-space: nowrap;
  }

  .holder {
    position: absolute;
    left: 26px;
    top: 187px;
    font-family: "Barlow Semi Condensed", sans-serif;
  }
  .holder__name { font-size: 18px; font-weight: 600; color: var(--maroon); line-height: 22px; }
  .holder__title { font-size: 12px; color: var(--ink); margin-top: 2px; }

  .contact-list {
    position: absolute;
    left: 267px;
    top: 189px;
    list-style: none;
    font-family: "Barlow Semi Condensed", sans-serif;
    font-size: 12.5px;
    font-weight: 500;
    color: var(--ink);
    white-space: nowrap;
  }
  .contact-list li {
    display: flex;
    align-items: center;
    gap: 7px;
    height: 17px;
  }
  .contact-list svg { width: 10px; height: 10px; fill: var(--icon); flex: none; }

  .base-rule {
    position: absolute;
    left: 0; right: 0; bottom: 0;
    height: 6px;
    background: var(--maroon);
  }
</style>
</head>
<body>
  <section class="card card--front">
    <div class="brand-name"><span class="brand-name__dot"></span>Tallowmere Comfort</div>
    <div class="service-band">Residential &amp; Light Commercial Heating &nbsp;• Air Conditioning Contractor</div>
  </section>

  <section class="card card--back">
    <div class="brand-name"><span class="brand-name__dot"></span>Tallowmere Comfort</div>
    <div class="holder">
      <div class="holder__name">Dominic Westerhall</div>
      <div class="holder__title">Managing Director</div>
    </div>
    <ul class="contact-list">
      <li><svg viewBox="0 0 12 12"><path d="M1 4c0-2 2-3 5-3s5 1 5 3l-2 1-1-2H4L3 5 1 4zM3 6h6l1 5H2z"/></svg>862-415-2736</li>
      <li><svg viewBox="0 0 12 12"><path d="M0 2h12v8H0zM1 3l5 4 5-4v-.2H1z" fill-rule="evenodd"/></svg>info@TallowmereLLC.example</li>
      <li><svg viewBox="0 0 12 12"><circle cx="6" cy="6" r="5.5"/><path d="M6 .5v11M.5 6h11M2 3h8M2 9h8" stroke="#f4f4f2" stroke-width="0.8" fill="none"/></svg>www.TallowmereLLC.example</li>
      <li><svg viewBox="0 0 12 12"><path d="M6 0a4 4 0 0 1 4 4c0 3-4 8-4 8S2 7 2 4a4 4 0 0 1 4-4zm0 2.5a1.5 1.5 0 1 0 0 3 1.5 1.5 0 0 0 0-3z" fill-rule="evenodd"/></svg>PO box 518 Brightwater NJ 07912</li>
    </ul>
    <div class="base-rule"></div>
  </section>
</body>
</html>
```